Business card for medical clinic

I need an upmarket, modern medical/health business card for my clinic

Contact Information for Business Card

name, address, email, qr code

```html
<!DOCTYPE html>
<html lang="en">
<head>
<meta charset="utf-8">
<title>Meridian Care Partners – Business Card</title>
<link href="https://fonts.googleapis.com/css2?family=Montserrat:wght@400;500;700&display=swap" rel="stylesheet">
<style>
  :root {
    --page-bg: #d9d4cc;
    --card-bg: #f1efeb;
    --card-edge: #ffffff;
    --ink-navy: #2a3648;
    --ink-teal: #1f6f82;
    --ink-body: #3b3f45;
  }
  * { box-sizing: border-box; margin: 0; padding: 0; }
  html, body {
    width: 1200px;
    height: 1200px;
    overflow: hidden;
    background: var(--page-bg);
    font-family: "Montserrat", sans-serif;
  }
  .business-card {
    position: absolute;
    left: 75px;
    top: 300px;
    width: 1050px;
    height: 600px;
    border-radius: 26px;
    background: var(--card-bg);
    border: 2px solid var(--card-edge);
    box-shadow: 0 10px 30px rgba(0,0,0,0.12);
    overflow: hidden;
  }
  .brand {
    position: absolute;
    left: 60px;
    top: 92px;
    display: flex;
    align-items: center;
    gap: 18px;
  }
  .brand-dot {
    width: 64px;
    height: 64px;
    border-radius: 50%;
    border: 5px solid var(--ink-teal);
  }
  .brand-name {
    font-weight: 500;
    font-size: 34px;
    letter-spacing: 2px;
    color: var(--ink-navy);
    text-transform: uppercase;
  }
  .accent-tab {
    position: absolute;
    left: -8px;
    top: 284px;
    width: 24px;
    height: 66px;
    border-radius: 0 10px 10px 0;
    background: linear-gradient(180deg, var(--ink-navy), var(--ink-teal));
  }
  .holder-name {
    position: absolute;
    left: 56px;
    top: 282px;
    font-weight: 700;
    font-size: 36px;
    letter-spacing: 1px;
    color: var(--ink-navy);
    text-transform: uppercase;
  }
  .holder-title {
    position: absolute;
    left: 56px;
    top: 330px;
    font-weight: 400;
    font-size: 24px;
    color: var(--ink-body);
  }
  .contact-list {
    position: absolute;
    left: 56px;
    top: 417px;
    list-style: none;
  }
  .contact-item {
    display: flex;
    align-items: center;
    gap: 14px;
    height: 39px;
    font-size: 25px;
    color: var(--ink-body);
  }
  .contact-icon { width: 22px; height: 22px; fill: var(--ink-teal); }
  .decor-ring {
    position: absolute;
    left: 650px;
    top: 20px;
    width: 560px;
    height: 560px;
    border-radius: 50%;
    border: 14px solid var(--ink-teal);
    opacity: 0.85;
  }
</style>
</head>
<body>
  <div class="business-card">
    <div class="decor-ring" aria-hidden="true"></div>

    <div class="brand">
      <span class="brand-dot" aria-hidden="true"></span>
      <span class="brand-name">Meridian Care Partners</span>
    </div>

    <span class="accent-tab" aria-hidden="true"></span>
    <h1 class="holder-name">Adrian Colmer</h1>
    <p class="holder-title">President</p>

    <ul class="contact-list">
      <li class="contact-item">
        <svg class="contact-icon" viewBox="0 0 24 24" aria-hidden="true"><path d="M6.6 10.8a15.1 15.1 0 0 0 6.6 6.6l2.2-2.2a1 1 0 0 1 1-.25 11.4 11.4 0 0 0 3.6.57 1 1 0 0 1 1 1V20a1 1 0 0 1-1 1A17 17 0 0 1 3 4a1 1 0 0 1 1-1h3.5a1 1 0 0 1 1 1c0 1.25.2 2.45.57 3.57a1 1 0 0 1-.25 1z"/></svg>
        <span>555-014-2871</span>
      </li>
      <li class="contact-item">
        <svg class="contact-icon" viewBox="0 0 24 24" aria-hidden="true"><path d="M2 5h20v14H2z M2 5l10 8 10-8" fill="none" stroke="currentColor"/><path d="M2 6.5V19h20V6.5l-10 7.5z"/></svg>
        <span>adrian@MeridianCare.com</span>
      </li>
      <li class="contact-item">
        <svg class="contact-icon" viewBox="0 0 24 24" aria-hidden="true"><path d="M12 2a10 10 0 1 0 0 20 10 10 0 0 0 0-20zm0 2c1.2 1.4 2 3.6 2.2 7H9.8C10 7.6 10.8 5.4 12 4zM4.1 13h3.7c.1 2.4.6 4.5 1.5 6A8 8 0 0 1 4.1 13zm0-2A8 8 0 0 1 9.3 5c-.9 1.5-1.4 3.6-1.5 6zm5.7 2h4.4c-.2 3.4-1 5.6-2.2 7-1.2-1.4-2-3.6-2.2-7zm4.9 6c.9-1.5 1.4-3.6 1.5-6h3.7a8 8 0 0 1-5.2 6zm1.5-8c-.1-2.4-.6-4.5-1.5-6a8 8 0 0 1 5.2 6z"/></svg>
        <span>www.MeridianCare.com</span>
      </li>
    </ul>
  </div>
</body>
</html>
```